Sales/Landing Page Redesign for Hunting product

I am looking for a redesign for https://ridgelynoutfitters.com/quarter-pad .

We want to add in the information for our new XL quarterpad found: https://ridgelynoutfitters.com/shop/hunting/xl-big-game-quarter-pad/

We also will be adding a spot for this video: https://www.vidstreamhub.com/watch?v=Zk4TnaR8wqe

We like having the 3 options at the bottom, but the goal for this page is to sell the quarter pad.

Target Market(s)

Western Hunters, campers, outdoorsmen

Industry/Entity Type

Hunting

Number of Pages Required

1 page

Font styles to use
Sans Serif

Requirements
Must have
• a clean design that is geared to sell the product.

```html
<!DOCTYPE html>
<html lang="en">
<head>
<meta charset="utf-8">
<title>Ridgelyn Quarter Pads</title>
<link rel="stylesheet" href="https://fonts.googleapis.com/css2?family=Rajdhani:wght@500;600;700&family=Open+Sans:ital,wght@0,400;0,600;1,400&display=swap">
<style>
:root{
  --navy:#0c1420;
  --red:#d6000f;
  --red-dark:#7a0008;
  --ink:#111111;
  --grey-bg:#efefef;
  --text:#444444;
  --line:#e4e4e4;
  --white:#ffffff;
}
*{box-sizing:border-box;margin:0;padding:0}
html,body{width:1200px;height:4758px;overflow:hidden}
body{font-family:"Open Sans",Arial,sans-serif;color:var(--text);background:var(--white);position:relative}
.head{font-family:"Rajdhani",Arial,sans-serif;font-weight:700;text-transform:uppercase;color:var(--ink)}
.accent{color:var(--red)}
.btn{display:inline-flex;align-items:center;justify-content:center;font-family:"Rajdhani",Arial,sans-serif;font-weight:700;text-transform:uppercase;background:var(--red);color:var(--white);text-decoration:none}
section,header,footer{position:absolute;left:0;width:1200px}

/* header */
.site-header{top:0;height:81px;background:var(--navy)}
.brand{position:absolute;font-family:"Rajdhani",sans-serif;font-weight:700;color:var(--white);letter-spacing:1px}
.site-header .brand{left:35px;top:27px;font-size:18px}
.nav-link{position:absolute;top:20px;height:39px;display:flex;align-items:center;font-family:"Rajdhani",sans-serif;font-weight:600;font-size:12px;letter-spacing:3px;color:#cfd3d8;text-transform:uppercase}
.nav-meals{left:781px}
.nav-pads{left:850px;width:146px;justify-content:center;background:#1b2533;border-radius:20px}
.nav-shop{left:1004px;width:107px;justify-content:center;background:var(--red);color:var(--white)}
.cart{position:absolute;left:1128px;top:20px;width:40px;height:40px;border-radius:50%;background:#3a4250}

/* hero */
.hero{top:81px;height:565px;overflow:hidden}
.hero-photo{position:absolute;inset:0;background:linear-gradient(180deg,#3d434a 0%,#5b4a36 40%,#6d5434 70%,#4a3624 100%)}
.hero-tarp{position:absolute;left:0;top:300px;width:560px;height:260px;background:linear-gradient(90deg,#c4541c,#a8401a);opacity:.75;border-radius:0 60% 0 0}
.hero-shade{position:absolute;inset:0;background:rgba(0,0,0,.35)}
.hero-title{position:absolute;top:126px;width:100%;text-align:center;color:var(--white);font-size:58px;line-height:58px}
.hero-tag{position:absolute;left:264px;top:266px;width:672px;height:43px;background:rgba(10,10,10,.75);color:var(--white);font-family:"Rajdhani",sans-serif;font-weight:700;font-size:24px;display:flex;align-items:center;justify-content:center;text-transform:uppercase}
.hero-btns{position:absolute;top:338px;left:445px;display:flex;gap:8px}
.hero-btns .btn{height:54px;font-size:18px}
.btn-learn{width:151px;background:#161616}
.btn-buy{width:149px}
.hero-slash{position:absolute;left:0;bottom:0}

/* video */
.video-sec{top:646px;height:674px;background:var(--grey-bg)}
.sec-title{position:absolute;width:100%;text-align:center;font-size:46px;line-height:46px}
.video-sec .sec-title{top:62px}
.video{position:absolute;left:238px;top:135px;width:722px;height:406px;background:linear-gradient(135deg,#3a2a1e,#5a4330 50%,#1d1713);overflow:hidden}
.video-bar{position:absolute;left:0;bottom:0;width:100%;height:32px;background:linear-gradient(transparent,rgba(0,0,0,.75))}
.video-bar span{position:absolute;left:100px;bottom:8px;font-size:9px;color:#ddd}
.video-track{position:absolute;left:10px;right:10px;bottom:26px;height:2px;background:rgba(255,255,255,.35)}
.play{position:absolute;left:337px;top:183px;width:48px;height:40px;border-radius:8px;background:rgba(20,20,20,.8)}

/* products */
.choose-sec{top:1320px;height:711px;background:var(--white)}
.choose-sec .sec-title{top:82px}
.card{position:absolute;top:194px;width:251px;height:395px;background:var(--white);box-shadow:0 2px 14px rgba(0,0,0,.12);text-align:center}
.bag{position:absolute;left:62px;top:40px;width:127px;height:140px;border-radius:40% 40% 30% 30%}
.price{position:absolute;top:210px;width:100%;color:var(--red);font-family:"Rajdhani",sans-serif;font-weight:700;font-size:20px}
.pname{position:absolute;top:248px;width:100%;font-family:"Rajdhani",sans-serif;font-weight:600;font-size:19px;line-height:26px;color:var(--ink);text-transform:uppercase}
.card .btn{position:absolute;left:59px;top:321px;width:132px;height:40px;font-size:18px}

/* responsible */
.resp-sec{top:2031px;height:624px;background:linear-gradient(90deg,#1a0a0a 0%,#4a0607 40%,#b3000c 80%,#c8000e 100%)}
.resp-title{position:absolute;left:170px;top:130px;color:var(--white);font-size:36px;line-height:40px}
.ticks{position:absolute;left:172px;top:237px;list-style:none}
.ticks li{display:flex;align-items:center;gap:8px;height:31.5px;font-family:"Rajdhani",sans-serif;font-weight:600;font-size:18px;color:var(--white)}
.tick{flex:none;width:22px;height:22px}
.resp-sec .btn-white{position:absolute;left:172px;top:450px;width:251px;height:52px;background:var(--white);color:var(--red);font-size:17px}
.resp-photo{position:absolute;left:657px;top:94px;width:436px;height:436px;border-radius:50%;background:radial-gradient(circle at 45% 45%,#f28a2a 0%,#c8661e 35%,#7a6a4a 70%,#4c4434 100%)}

/* testimonials */
.say-sec{top:2655px;height:779px;background:var(--white)}
.say-sec .sec-title{top:77px}
.quote{position:absolute;width:240px;text-align:center}
.qmark{font-family:"Rajdhani",sans-serif;font-weight:700;font-size:64px;line-height:40px;color:var(--ink);height:40px}
.qtext{margin-top:18px;font-style:italic;font-size:11.5px;line-height:19px;color:#555}
.qname{position:absolute;left:0;width:100%;font-family:"Rajdhani",sans-serif;font-weight:700;font-size:14px;color:var(--red)}
.divider-v{position:absolute;width:1px;background:var(--line)}
.divider-h{position:absolute;height:1px;background:var(--line)}

/* still */
.still-sec{top:3434px;height:618px;overflow:hidden;background:linear-gradient(90deg,#7c7a5a 0%,#a7a58a 30%,#e6e6e6 55%,#f2f2f2 100%)}
.still-fade{position:absolute;right:0;top:0;width:700px;height:100%;background:linear-gradient(90deg,rgba(245,245,245,0),rgba(245,245,245,.85) 30%)}
.still-title{position:absolute;left:668px;top:138px;font-size:46px;line-height:46px}
.still-list{position:absolute;left:660px;top:205px;list-style:none}
.still-list li{display:flex;align-items:center;gap:10px;height:33px;font-family:"Rajdhani",sans-serif;font-weight:600;font-size:19px;color:#333}
.still-list li.plain{padding-left:32px}
.still-sec .btn{position:absolute;left:659px;top:420px;width:251px;height:52px;font-size:17px}

/* features */
.feat-sec{top:4052px;height:452px;background:var(--white)}
.feat{position:absolute;top:0;width:320px;text-align:center}
.feat svg{position:absolute;left:130px;top:72px}
.feat h3{position:absolute;top:158px;width:100%;font-size:27px;line-height:33px}
.feat p{position:absolute;top:248px;left:50px;width:220px;font-size:11.5px;line-height:18.5px;color:#555}
.feat .btn{position:absolute;left:68px;top:356px;width:185px;height:41px;font-size:11px;font-family:"Open Sans",sans-serif}

/* footer */
.site-footer{top:4504px;height:254px;background:var(--navy)}
.site-footer .brand{top:58px;width:100%;text-align:center;font-size:16px}
.socials{position:absolute;top:90px;left:598px;display:flex;gap:18px}
.socials span{width:14px;height:14px;border-radius:50%;background:#dfe2e6}
.copy{position:absolute;top:114px;width:100%;text-align:center;font-size:9px;letter-spacing:2px;color:#4b5563}
.foot-links{position:absolute;top:158px;left:227px;display:flex;gap:44px;font-size:12px;color:var(--red)}
</style>
</head>
<body>

<header class="site-header">
  <div class="brand">RIDGELYN</div>
  <div class="nav-link nav-meals">Meals</div>
  <div class="nav-link nav-pads">Quarter Pads</div>
  <div class="nav-link nav-shop">Shop Now</div>
  <div class="cart"></div>
</header>

<section class="hero">
  <div class="hero-photo" role="img" aria-label="Game quarters resting on an orange quarter pad in a dry field at dusk"></div>
  <div class="hero-tarp"></div>
  <div class="hero-shade"></div>
  <h1 class="head hero-title">Quarter Pads to<br>Keep Your Meat Clean</h1>
  <div class="hero-tag">• 100% Waterproof • Lightweight • Quality Guarantee</div>
  <div class="hero-btns">
    <a class="btn btn-learn" href="#">Learn More</a>
    <a class="btn btn-buy" href="#">Buy Now</a>
  </div>
  <svg class="hero-slash" width="1200" height="70" viewBox="0 0 1200 70">
    <polygon points="0,70 0,45 200,28 700,18 1200,0 1200,70" fill="var(--red)"/>
    <polygon points="0,70 0,62 600,52 1200,42 1200,70" fill="var(--grey-bg)"/>
  </svg>
</section>

<section class="video-sec">
  <h2 class="head sec-title">Our <span class="accent">Video</span></h2>
  <div class="video" role="img" aria-label="Product video: a hunter in a cap explains the quarter pad in front of a wooden wall">
    <div class="play"><svg width="48" height="40"><polygon points="20,13 20,27 31,20" fill="#fff"/></svg></div>
    <div class="video-track"></div>
    <div class="video-bar"><span>0:00 / 1:25</span></div>
  </div>
</section>

<section class="choose-sec">
  <h2 class="head sec-title">Choose Your <span class="accent">Quarter Pad</span></h2>
  <div class="card" style="left:52px">
    <div class="bag" style="background:#c8161d" role="img" aria-label="Red quarter pad stuff sack"></div>
    <div class="price">$19.99</div>
    <div class="pname">Red<br>Quarter Pad</div>
    <a class="btn" href="#">Buy Now</a>
  </div>
  <div class="card" style="left:334px">
    <div class="bag" style="background:#f36c21" role="img" aria-label="Orange quarter pad stuff sack"></div>
    <div class="price">$19.99</div>
    <div class="pname">Orange<br>Quarter Pad</div>
    <a class="btn" href="#">Buy Now</a>
  </div>
  <div class="card" style="left:617px">
    <div class="bag" style="background:#1fa34a" role="img" aria-label="Green XL big game quarter pad stuff sack"></div>
    <div class="price">$19.99</div>
    <div class="pname">XL Big Game<br>Quarter Pad</div>
    <a class="btn" href="#">Buy Now</a>
  </div>
  <div class="card" style="left:899px">
    <div class="bag" style="background:#f36c21" role="img" aria-label="Orange XL big game quarter pad stuff sack"></div>
    <div class="price">$29.99</div>
    <div class="pname">XL Big Game<br>Quarter Pad</div>
    <a class="btn" href="#">Buy Now</a>
  </div>
</section>

<section class="resp-sec">
  <h2 class="head resp-title" style="color:var(--white)">Be Responsible. Use<br>A Quarter Pad.</h2>
  <ul class="ticks">
    <li><svg class="tick" viewBox="0 0 22 22"><circle cx="11" cy="11" r="11" fill="#fff"/><polyline points="6,11.5 9.5,15 16,8" fill="none" stroke="#8a0009" stroke-width="2.4"/></svg>Keep your meat off the dirt</li>
    <li><svg class="tick" viewBox="0 0 22 22"><circle cx="11" cy="11" r="11" fill="#fff"/><polyline points="6,11.5 9.5,15 16,8" fill="none" stroke="#8a0009" stroke-width="2.4"/></svg>Lightweight</li>
    <li><svg class="tick" viewBox="0 0 22 22"><circle cx="11" cy="11" r="11" fill="#fff"/><polyline points="6,11.5 9.5,15 16,8" fill="none" stroke="#8a0009" stroke-width="2.4"/></svg>100% Waterproof</li>
    <li><svg class="tick" viewBox="0 0 22 22"><circle cx="11" cy="11" r="11" fill="#fff"/><polyline points="6,11.5 9.5,15 16,8" fill="none" stroke="#8a0009" stroke-width="2.4"/></svg>Reusable</li>
    <li><svg class="tick" viewBox="0 0 22 22"><circle cx="11" cy="11" r="11" fill="#fff"/><polyline points="6,11.5 9.5,15 16,8" fill="none" stroke="#8a0009" stroke-width="2.4"/></svg>55"X60" WHEN OPEN</li>
    <li><svg class="tick" viewBox="0 0 22 22"><circle cx="11" cy="11" r="11" fill="#fff"/><polyline points="6,11.5 9.5,15 16,8" fill="none" stroke="#8a0009" stroke-width="2.4"/></svg>Respect the animal by keeping it contamination free.</li>
  </ul>
  <a class="btn btn-white" href="#">Select My Quarter Pad</a>
  <div class="resp-photo" role="img" aria-label="Orange quarter pad sack clipped to a hunting backpack strap"></div>
</section>

<section class="say-sec">
  <h2 class="head sec-title">What Others <span class="accent">Are Saying</span></h2>
  <div class="divider-v" style="left:436px;top:197px;height:450px"></div>
  <div class="divider-v" style="left:753px;top:197px;height:450px"></div>
  <div class="divider-h" style="left:172px;top:409px;width:853px"></div>

  <div class="quote" style="left:163px;top:212px;height:190px">
    <div class="qmark">“</div>
    <p class="qtext">A must have for any hunter. Keeping meat clean from field to freezer, priceless!</p>
    <div class="qname" style="top:150px">Caleb Marsh</div>
  </div>
  <div class="quote" style="left:480px;top:212px;height:190px">
    <div class="qmark">“</div>
    <p class="qtext">This is something that is needed on every hunt! Light easy to carry and a necessity to keep your hard earned meat clean!</p>
    <div class="qname" style="top:150px">Wade Hollis</div>
  </div>
  <div class="quote" style="left:789px;top:212px;height:190px">
    <div class="qmark">“</div>
    <p class="qtext">There is no better light weight option out there to keep your meat &amp; cape clean after a successful hunt.</p>
    <div class="qname" style="top:150px">Trent Albrey - @trent_afield</div>
  </div>

  <div class="quote" style="left:163px;top:456px;height:200px">
    <div class="qmark">“</div>
    <p class="qtext">Gone are the days of struggling to keep a quarter from sliding off a log or rock while trying to de-bone meat. Packs small, weighs nothing, and keeps meat perfectly clean. It's in my pack 100% of the time. Great Product!</p>
    <div class="qname" style="top:170px">Dana Whitcomb</div>
  </div>
  <div class="quote" style="left:480px;top:456px;height:200px">
    <div class="qmark">“</div>
    <p class="qtext">The Quarter Pad is a game changer when it comes to cleanliness in the hills. Lightweight, and compacts down super small! No more getting dirt and pine needles all over your meat.</p>
    <div class="qname" style="top:170px">Rowan Pike - @highcountrytrails</div>
  </div>
  <div class="quote" style="left:789px;top:456px;height:200px">
    <div class="qmark">“</div>
    <p class="qtext">The Quarter Pads keep your meat clean and double up as a waterproof poncho and ground tarp. They are a must have for any serious hunter.</p>
    <div class="qname" style="top:170px">Eli Brandvold</div>
  </div>
</section>

<section class="still-sec">
  <div class="still-fade"></div>
  <svg style="position:absolute;left:175px;top:82px" width="444" height="470" viewBox="0 0 444 470" role="img" aria-label="Hunter kneeling beside a quarter pad at sunset, framed in a red hexagon">
    <defs>
      <linearGradient id="sunset" x1="0" y1="0" x2="0" y2="1">
        <stop offset="0" stop-color="#5a5a52"/>
        <stop offset="0.45" stop-color="#e0801e"/>
        <stop offset="1" stop-color="#5e4a32"/>
      </linearGradient>
    </defs>
    <polygon points="222,0 444,117 444,353 222,470 0,353 0,117" fill="var(--red)"/>
    <polygon points="222,16 428,126 428,344 222,454 16,344 16,126" fill="url(#sunset)"/>
  </svg>
  <h2 class="head still-title">Do You Still...</h2>
  <ul class="still-list">
    <li><svg class="tick" viewBox="0 0 22 22"><circle cx="11" cy="11" r="11" fill="var(--red)"/><polyline points="6,11.5 9.5,15 16,8" fill="none" stroke="#fff" stroke-width="2.4"/></svg>Lay your fresh meat on a rock?</li>
    <li><svg class="tick" viewBox="0 0 22 22"><circle cx="11" cy="11" r="11" fill="var(--red)"/><polyline points="6,11.5 9.5,15 16,8" fill="none" stroke="#fff" stroke-width="2.4"/></svg>Sew bed sheets together?</li>
    <li><svg class="tick" viewBox="0 0 22 22"><circle cx="11" cy="11" r="11" fill="var(--red)"/><polyline points="6,11.5 9.5,15 16,8" fill="none" stroke="#fff" stroke-width="2.4"/></svg>use a blue tarp?</li>
    <li><svg class="tick" viewBox="0 0 22 22"><circle cx="11" cy="11" r="11" fill="var(--red)"/><polyline points="6,11.5 9.5,15 16,8" fill="none" stroke="#fff" stroke-width="2.4"/></svg>lay your meat in the dirt?</li>
    <li><svg class="tick" viewBox="0 0 22 22"><circle cx="11" cy="11" r="11" fill="var(--red)"/><polyline points="6,11.5 9.5,15 16,8" fill="none" stroke="#fff" stroke-width="2.4"/></svg>stuff the meat in old used pillow cases?</li>
    <li class="plain">...There is a better way</li>
  </ul>
  <a class="btn" href="#">Select My Quarter Pad</a>
</section>

<section class="feat-sec">
  <div class="divider-v" style="left:436px;top:0;height:452px"></div>
  <div class="divider-v" style="left:766px;top:0;height:452px"></div>

  <div class="feat" style="left:110px">
    <svg width="60" height="66" viewBox="0 0 60 66"><path d="M30 3 L55 12 V32 C55 48 44 58 30 63 C16 58 5 48 5 32 V12 Z" fill="none" stroke="var(--red)" stroke-width="3.5"/><circle cx="30" cy="33" r="11" fill="none" stroke="var(--red)" stroke-width="3"/><polyline points="24,33 28.5,37.5 36,29" fill="none" stroke="var(--red)" stroke-width="3"/></svg>
    <h3 class="head">30 Day<br>Guarantee</h3>
    <p>If for any reason, within 30 days from date of purchase, you are not completely satisfied with your order we will refund the purchase price upon receipt of the return shipment.</p>
    <a class="btn" href="#">Warranty Information</a>
  </div>
  <div class="feat" style="left:440px">
    <svg width="66" height="66" viewBox="0 0 66 66"><circle cx="33" cy="20" r="15" fill="none" stroke="var(--red)" stroke-width="3.5"/><path d="M6 64 C6 46 18 38 33 38 C48 38 60 46 60 64" fill="none" stroke="var(--red)" stroke-width="3.5"/></svg>
    <h3 class="head">Our<br>Retailers</h3>
    <p>Visit any of our dealer locations and experience first hand the quality and thought that goes into assuring your next adventure is a success.</p>
    <a class="btn" href="#">Find a Dealer</a>
  </div>
  <div class="feat" style="left:769px">
    <svg width="66" height="66" viewBox="0 0 66 66"><circle cx="33" cy="33" r="30" fill="none" stroke="var(--red)" stroke-width="3.5"/><path d="M24 25 C24 18 29 15 33 15 C38 15 42 18 42 24 C42 31 33 31 33 39" fill="none" stroke="var(--red)" stroke-width="4"/><circle cx="33" cy="48" r="3" fill="var(--red)"/></svg>
    <h3 class="head">Have<br>Questions?</h3>
    <p>We have answers. Feel free to reach out to our dedicated support staff to get answers. Assuring your preparation for your next outdoor adventure is simple is what we do.</p>
    <a class="btn" href="#">Contact Us</a>
  </div>
</section>

<footer class="site-footer">
  <div class="brand">RIDGELYN</div>
  <div class="socials"><span></span><span></span></div>
  <div class="copy">COPYRIGHT © 2023</div>
  <div class="foot-links">
    <span>My Account</span><span>Blog</span><span>Terms of Service Agreement</span><span>Refund and Return Policy</span><span>Privacy Policy Agreement</span>
  </div>
</footer>

</body>
</html>
```